Web Design Project for a beach town business owner who supports new families with their babies.

I'm looking for a basic website with the following pages: home, about, services, FAQs, blog, and contact page. I have images and content ready to go.

Target Market(s)

Men and women between the ages of 22 and 42, growing families

Industry/Entity Type

Postpartum Doula

Coding

Number of Pages Required

Font styles to use
Serif
Other font styles liked:
• My logo font is "Nexa Bold" - so coordinating fonts with that are ideal

Colors
00AB8E
00BBA5
67D7C9
C6EFE9
E9F9F6
EE7325
F08F49
F5BC92
FAE3D3
FDF4ED

Requirements
Must have
• Warm and professional vibe, multicultural images, aligned with my branding colors and font ("Nexa Bold"; COLORS: light blue hex: #2FCEC2 R: 47 G: 206 B: 194 dark blue hex: #007C7C R: 0 G: 124 B: 124 orange hex: #F77B4E R: 247 G: 123 B: 78), good SEO
Should not have
• Ultra feminine images, baby bottles, cutesy images.

```html
<!DOCTYPE html>
<html lang="en">
<head>
<meta charset="utf-8">
<title>Harborlight Families Postpartum Care</title>
<link href="https://fonts.googleapis.com/css2?family=Montserrat:wght@400;600;700;800&family=Nunito+Sans:wght@400;600&display=swap" rel="stylesheet">
<style>
  :root {
    --teal: #00bba5;
    --teal-deep: #00998c;
    --teal-dark: #007c7c;
    --teal-light: #67d7c9;
    --orange: #f77b4e;
    --orange-soft: #f08f49;
    --ink: #333333;
    --footer: #2f3233;
    --white: #ffffff;
  }
  * { margin: 0; padding: 0; box-sizing: border-box; }
  html, body { width: 1200px; height: 3196px; overflow: hidden; background: var(--white); }
  body { position: relative; font-family: "Nunito Sans", Arial, sans-serif; color: var(--ink); }
  .abs { position: absolute; }

  /* Hero */
  .hero { left: 0; top: 0; width: 1200px; height: 730px;
    background: linear-gradient(180deg, #3a3a3a 0%, #1f1f1f 55%, #2b2b2b 100%); }
  .hero-overlay { left: 0; top: 0; width: 1200px; height: 730px; background: rgba(0,0,0,.25); }
  .brand { left: 70px; top: 22px; display: flex; align-items: center; gap: 14px; }
  .brand-mark { width: 150px; height: 150px; border-radius: 50%; background: var(--teal);
    border: 6px solid var(--white); display: flex; align-items: center; justify-content: center;
    font-family: "Montserrat", sans-serif; font-weight: 700; font-size: 17px; color: var(--white);
    text-align: center; line-height: 1.25; padding: 14px; }
  .main-nav { right: 60px; top: 76px; display: flex; align-items: center; gap: 34px; list-style: none; }
  .main-nav a { font-family: "Montserrat", sans-serif; font-weight: 700; font-size: 17px;
    color: var(--white); text-decoration: none; letter-spacing: .5px; }
  .main-nav .is-active { background: var(--teal); padding: 13px 30px; border-radius: 30px; }
  .hero-copy { left: 0; width: 1200px; top: 468px; text-align: center; }
  .hero-kicker { font-family: "Montserrat", sans-serif; font-weight: 700; font-size: 40px; color: var(--teal); }
  .hero-title { font-family: "Montserrat", sans-serif; font-weight: 800; font-size: 40px;
    color: var(--white); line-height: 1.25; margin-top: 4px; }

  /* Intro */
  .intro-title { left: 100px; width: 1000px; top: 808px; text-align: center;
    font-family: "Montserrat", sans-serif; font-weight: 700; font-size: 27px; line-height: 1.4; color: var(--teal); }
  .portrait { border-radius: 50%; border: 10px solid var(--teal); }
  .portrait-fill { width: 100%; height: 100%; border-radius: 50%; }
  .intro-photo { left: 150px; top: 930px; width: 380px; height: 380px; }
  .intro-text { left: 612px; top: 948px; width: 480px; font-size: 16.5px; line-height: 1.62; }
  .intro-text p + p { margin-top: 22px; }

  /* Support band */
  .support-band { left: 0; top: 1430px; width: 1200px; height: 900px; }
  .support-title { left: 150px; width: 900px; top: 1592px; text-align: center; color: var(--white);
    font-family: "Montserrat", sans-serif; font-weight: 700; font-size: 27px; line-height: 1.45; }
  .support-photo { left: 410px; top: 1830px; width: 390px; height: 390px; border-color: var(--white); }
  .support-item { width: 200px; color: var(--white); font-size: 13.5px; line-height: 1.5; }
  .support-icon { width: 92px; height: 92px; border-radius: 50%; background: var(--orange);
    border: 5px solid var(--white); display: flex; align-items: center; justify-content: center; }
  .connector { height: 2px; background: var(--white); }

  /* Closing */
  .closing-photo { left: 60px; top: 2335px; width: 480px; height: 480px; }
  .closing-text { left: 620px; top: 2368px; width: 520px; font-size: 16.5px; line-height: 1.62; }
  .closing-text p + p { margin-top: 22px; }
  .cta { left: 620px; top: 2738px; width: 255px; height: 64px; border-radius: 34px; background: var(--orange);
    color: var(--white); font-family: "Montserrat", sans-serif; font-weight: 700; font-size: 18px;
    display: flex; align-items: center; justify-content: center; text-decoration: none; }

  /* Footer */
  .site-footer { left: 0; top: 2950px; width: 1200px; height: 246px; background: var(--footer); }
  .footer-nav { left: 0; width: 1200px; top: 3016px; display: flex; justify-content: center; gap: 44px; list-style: none; }
  .footer-nav a { color: var(--white); text-decoration: none; font-family: "Montserrat", sans-serif; font-weight: 600; font-size: 15px; }
  .copyright { left: 0; width: 1200px; top: 3066px; text-align: center; color: var(--white); font-size: 14px; }
  .social { left: 0; width: 1200px; top: 3112px; display: flex; justify-content: center; gap: 12px; }
  .social span { width: 34px; height: 34px; border-radius: 50%; border: 2px solid #cfcfcf; }
</style>
</head>
<body>

<header>
  <div class="abs hero" role="img" aria-label="Black and white photo of a parent holding a newborn baby"></div>
  <div class="abs hero-overlay"></div>
  <div class="abs brand"><div class="brand-mark">Harborlight Families</div></div>
  <nav>
    <ul class="abs main-nav">
      <li><a class="is-active" href="#">HOME</a></li>
      <li><a href="#">ABOUT</a></li>
      <li><a href="#">SERVICES</a></li>
      <li><a href="#">FAQS</a></li>
      <li><a href="#">BLOG</a></li>
      <li><a href="#">CONTACT</a></li>
    </ul>
  </nav>
  <div class="abs hero-copy">
    <p class="hero-kicker">Congratulations on your birth &amp;</p>
    <h1 class="hero-title">WELCOME TO HARBORLIGHT FAMILIES<br>POSTPARTUM CARE!</h1>
  </div>
</header>

<main>
  <section class="intro">
    <h2 class="abs intro-title">Hi, I'm Dana Reyes, a certified postpartum care expert and educator serving families of all varieties in the greater San Diego area and beyond.</h2>
    <div class="abs portrait intro-photo"><div class="portrait-fill" role="img" aria-label="Portrait of the postpartum care expert smiling" style="background:linear-gradient(160deg,#8fb7c4,#3e6f86 60%,#2a4f63);"></div></div>
    <div class="abs intro-text">
      <p>My passion as a professional is showing new parents just like you that whether you've just had your first child or your fifth, you cannot only survive your postpartum period (also known as the 4th trimester), but you and your family can THRIVE – with the kind of compassionate, skilled, and targeted support for your unique needs that only an expert can provide.<br>That's where I come in.</p>
      <p>Did you know that, on average, new parents won't see their midwife or obstetrician until 6 weeks after giving birth to their baby(ies)? Working with a postpartum care expert (also known as a doula) can help fill in this gap in continuity of care by providing individualized support for parents and families as they transition to life with their new baby.</p>
    </div>
  </section>

  <section class="support">
    <svg class="abs support-band" width="1200" height="900" viewBox="0 0 1200 900" aria-hidden="true">
      <path d="M0 70 Q600 -40 1200 70 L1200 790 Q600 900 0 790 Z" fill="var(--teal-deep)"/>
    </svg>
    <h2 class="abs support-title">My work includes four key areas of support that are designed to positively impact your postpartum period with your baby:</h2>
    <div class="abs portrait support-photo"><div class="portrait-fill" role="img" aria-label="Photo of the doula holding a sleeping newborn" style="background:linear-gradient(170deg,#efe8e4,#b8a9a6 55%,#5a4444);"></div></div>

    <div class="abs connector" style="left:362px;top:1926px;width:60px;"></div>
    <div class="abs connector" style="left:362px;top:2126px;width:60px;"></div>
    <div class="abs connector" style="left:788px;top:1926px;width:60px;"></div>
    <div class="abs connector" style="left:788px;top:2126px;width:60px;"></div>

    <p class="abs support-item" style="left:50px;top:1876px;">I provide practical, evidence-based information about baby care and help identify what is normal and what is outside the range of normal for parent(s) and baby.</p>
    <div class="abs support-icon" style="left:272px;top:1880px;">
      <svg width="40" height="40" viewBox="0 0 40 40" fill="none" stroke="#fff" stroke-width="2.5"><path d="M20 34s-13-8-13-17a7 7 0 0 1 13-3 7 7 0 0 1 13 3c0 9-13 17-13 17z"/></svg>
    </div>
    <p class="abs support-item" style="left:50px;top:2076px;">I am bonding and attachment between parent(s) and baby in the areas of feeding, soothing, learning baby's cues, babywearing, and playing with baby.</p>
    <div class="abs support-icon" style="left:272px;top:2080px;">
      <svg width="40" height="40" viewBox="0 0 40 40" fill="none" stroke="#fff" stroke-width="2.5"><circle cx="14" cy="14" r="5"/><circle cx="27" cy="16" r="4"/><path d="M5 32c0-6 4-10 9-10s9 4 9 10M22 32c0-5 2-8 5-8s6 3 6 8"/></svg>
    </div>

    <div class="abs support-icon" style="left:836px;top:1880px;">
      <svg width="40" height="40" viewBox="0 0 40 40" fill="none" stroke="#fff" stroke-width="2.5"><path d="M10 21l7 7 14-15"/></svg>
    </div>
    <p class="abs support-item" style="left:948px;top:1876px;">I prioritize the mental and emotional health of parent(s) and help identify potential warning signs that indicate that medical care may be needed.</p>
    <div class="abs support-icon" style="left:836px;top:2080px;">
      <svg width="40" height="40" viewBox="0 0 40 40" fill="none" stroke="#fff" stroke-width="2.5"><path d="M6 19l14-11 14 11M10 16v17h20V16"/></svg>
    </div>
    <p class="abs support-item" style="left:948px;top:2076px;">I offer hands-on support with baby(ies), older siblings, pets, overnight cover, upkeep, and meal preparation.</p>
  </section>

  <section class="closing">
    <div class="abs portrait closing-photo"><div class="portrait-fill" role="img" aria-label="Photo of a smiling family gathered around their newborn" style="background:linear-gradient(150deg,#d9d2cf,#8d7a75 50%,#3d3333);"></div></div>
    <div class="abs closing-text">
      <p>Families who work with me report feeling more connected, happy, and informed than their parenting veteran friends and family members – both during the time that I work with them and beyond.</p>
      <p>Struggle is a normal part of growth and learning. Your postpartum period is a time for healing and recovering from birth, bonding with your baby, and establishing a healthy feeding relationship in whatever way works best for your family. Let me show you how to remove the struggle from this magical time!</p>
    </div>
    <a class="abs cta" href="#">Let's Get Started</a>
  </section>
</main>

<footer>
  <div class="abs site-footer"></div>
  <ul class="abs footer-nav">
    <li><a href="#">HOME</a></li>
    <li><a href="#">ABOUT</a></li>
    <li><a href="#">SERVICES</a></li>
    <li><a href="#">FAQS</a></li>
    <li><a href="#">BLOG</a></li>
    <li><a href="#">CONTACT</a></li>
  </ul>
  <p class="abs copyright">Copyright © 2021 Company Name All Rights Reserved</p>
  <div class="abs social" aria-label="Social links"><span></span><span></span><span></span><span></span><span></span></div>
</footer>

</body>
</html>
```